New Pump Website Design Needed

We need a homepage concept for a pump website rebuild.

The navigation at the top must be:
Home - About Us - Pump Stations - Pumps - Electrical - Drainage - Environmental - Accessories - Contact Us

The homepage should have the the following structure:
Logo
Navigation
Rotating Banner
Content + Picture of PDF Flipbook to download/ view
Featured Products (in one row - approx 4)
Footer

The footer must include:
Left side - navigation small.
"Copyright KelvoRun 2014. All Rights reserved"

Right side: "Website by Pixel Orchard Studio"

Content and imagery, and Logo can be taken from their existing website: tarnbrookvalves.co.nz

We have attached a copy of their New PDF - the new website design must reflect this (Use block colours/ different colours for the navigation items/ incorporate the footer image).

Industry/Entity Type

Electrical

Font styles to use
Sans Serif

Requirements
Must have
• Features from their brochure brought in (colour scheme and footer feature)
Should not have
• Any Social Media Icons

```html
<!DOCTYPE html>
<html lang="en">
<head>
<meta charset="utf-8">
<title>KelvoRun Pump Systems</title>
<link rel="stylesheet" href="https://fonts.googleapis.com/css2?family=Arimo:wght@400;700&family=Open+Sans:wght@400;600&display=swap">
<style>
:root{
  --blue:#2a84c9;
  --blue-deep:#1c5e99;
  --nav:#1f5d95;
  --yellow:#f2c62e;
  --yellow-deep:#d9a514;
  --grey-bg:#ebebeb;
  --text:#6b6b6b;
  --dark:#231f20;
  --white:#ffffff;
}
*{margin:0;padding:0;box-sizing:border-box}
html,body{width:895px;height:1200px;overflow:hidden;background:var(--white)}
body{position:relative;font-family:"Arimo",Arial,sans-serif;color:var(--text)}
.abs{position:absolute}

.brand{left:76px;top:28px;font-weight:700;font-size:30px;color:var(--blue-deep);letter-spacing:1px;display:flex;align-items:center;gap:10px}
.brand-mark{width:16px;height:16px;background:var(--blue-deep)}
.tagline{left:102px;top:66px;font-size:11px;color:#222}
.contact{right:75px;top:34px;color:#555;text-align:right}
.contact .phone{display:flex;align-items:center;justify-content:flex-end;gap:6px;font-size:15px;margin-bottom:6px}
.contact .mail{font-size:12px;color:#444}

.nav{left:0;top:98px;width:895px;height:34px;background:linear-gradient(#2a6aa8,var(--nav))}
.nav-list{position:absolute;left:75px;right:75px;top:11px;display:flex;justify-content:space-between;list-style:none}
.nav-list a{font-size:10.5px;font-weight:700;color:var(--white);text-decoration:none;letter-spacing:.3px;white-space:nowrap}

.banner{left:0;top:132px;width:895px;height:346px;background:linear-gradient(120deg,#cfc6b3 0%,#e7dfcf 35%,#b9ae99 60%,#e8e1d2 80%,#a39780 100%)}
.arrow{width:42px;height:42px;border-radius:50%;background:rgba(255,255,255,.85);top:280px}

.content{left:0;top:478px;width:895px;height:383px;background:var(--grey-bg)}
.welcome{left:76px;top:508px;font-size:21px;font-weight:700;color:var(--blue)}
.photo{background:linear-gradient(135deg,#b8ad98,#5c6f8e 55%,#c7bca8)}
.intro-photo{left:76px;top:557px;width:192px;height:118px}
.body-text{font-size:10px;line-height:20px;text-align:justify;color:var(--text);hyphens:auto;-webkit-hyphens:auto}
.para-side{left:288px;top:556px;width:232px;height:120px;overflow:hidden}
.para-full{left:76px;top:684px;width:444px}
.divider{left:557px;top:533px;width:1px;height:310px;background:#cfcfcf}

.flip-head{left:587px;top:510px;width:228px;height:35px;background:var(--yellow);border-top:3px solid var(--blue);font-size:13px;color:#222;padding:9px 0 0 35px}
.flip-box{left:591px;top:545px;width:221px;height:291px;background:var(--blue);padding:14px 0 0 31px;color:var(--white)}
.flip-box h3{font-weight:400;font-size:15px;line-height:16px;color:#12365a;margin-bottom:8px}
.flip-box ul{list-style:none;font-family:"Open Sans",sans-serif;font-size:8.6px;line-height:13.4px;color:#dcecfa}
.flip-box li::before{content:"» "}
.flip-rule{position:absolute;left:31px;right:14px;top:207px;height:1px;background:#4d9ad6}
.download{left:595px;top:768px;width:213px;height:56px;border-radius:6px;background:linear-gradient(var(--yellow),var(--yellow-deep))}
.download b{position:absolute;left:19px;top:6px;font-size:24px;color:#111;letter-spacing:.5px}
.download span{position:absolute;left:52px;top:32px;font-size:16px;color:var(--white)}

.card{width:232px;height:195px;top:900px;border:1px solid #e2e2e2;background:var(--white);box-shadow:0 0 3px rgba(0,0,0,.08)}
.card h2{position:absolute;left:14px;top:5px;font-weight:400;font-size:15px;color:#222}
.card .photo{position:absolute;left:11px;top:31px;width:212px;height:86px}
.card p{position:absolute;left:8px;top:121px;width:218px;font-family:"Open Sans",sans-serif;font-size:8.2px;line-height:13.4px;color:#222}
.more{position:absolute;right:12px;top:170px;width:63px;height:17px;border-radius:3px;background:linear-gradient(#4a9fe0,var(--blue));font-size:8.5px;color:var(--white);text-align:center;line-height:17px}

.footer{left:2px;top:1130px;width:893px;height:70px;background:var(--dark);border-top:6px solid #555}
.foot-nav{left:75px;top:1150px;font-size:10px;color:#e0e0e0;letter-spacing:.2px;white-space:nowrap}
.foot-copy{left:75px;top:1167px;font-size:9.5px;color:#e0e0e0}
.foot-credit{right:75px;top:1153px;font-size:9.5px;color:#e0e0e0}
</style>
</head>
<body>
<header>
  <div class="abs brand"><span class="brand-mark"></span>KelvoRun</div>
  <div class="abs tagline">Providing Pumping Solutions</div>
  <div class="abs contact">
    <div class="phone"><svg width="24" height="18" viewBox="0 0 24 18"><path d="M2 6 Q12 -2 22 6 L19 8 L16 6 L16 4 Q12 2 8 4 L8 6 L5 8 Z" fill="#555"/><rect x="5" y="9" width="14" height="8" rx="2" fill="#555"/><circle cx="12" cy="13" r="2.4" fill="#fff"/></svg>(555)-204-718</div>
    <div class="mail">E-mail: info@kelvorun.com</div>
  </div>
</header>

<nav class="abs nav">
  <ul class="nav-list">
    <li><a>HOME</a></li><li><a>ABOUT US</a></li><li><a>PUMP STATIONS</a></li><li><a>PUMPS</a></li><li><a>ELECTRICAL</a></li><li><a>DRAINAGE</a></li><li><a>ENVIRONMENTAL</a></li><li><a>ACCESSORIES</a></li><li><a>CONTACT US</a></li>
  </ul>
</nav>

<section class="abs banner" role="img" aria-label="Large beige pump valves with blue flanges at a pump station"></section>
<svg class="abs arrow" style="left:32px" viewBox="0 0 42 42"><path d="M25 12 L16 21 L25 30" stroke="#222" stroke-width="4" fill="none"/></svg>
<svg class="abs arrow" style="left:821px" viewBox="0 0 42 42"><path d="M17 12 L26 21 L17 30" stroke="#222" stroke-width="4" fill="none"/></svg>

<main>
  <div class="abs content"></div>
  <h1 class="abs welcome">Welcome To KelvoRun Pump Systems</h1>
  <div class="abs photo intro-photo" role="img" aria-label="Technician assembling a blue pump shaft on site"></div>
  <p class="abs body-text para-side">Lorem ipsum dolor sit amet, consectetur adipisicing elit, sed do eiusmod tempor incididunt ut labore et dolore magna aliqua. Ut enim ad minim veniam, quis nostrud exercitation ullamco laboris nisi ut aliquip ex ea commodo consequat. Duis aute irure dolor in reprehenderit in voluptate velit</p>
  <p class="abs body-text para-full">Lorem ipsum dolor sit amet, consectetur adipisicing elit, sed do eiusmod tempor incididunt ut labore et dolore magna aliqua. Ut enim ad minim veniam, quis nostrud exercitation ullamco laboris nisi ut aliquip ex ea commodo consequat. Duis aute irure dolor in reprehenderit in voluptate velit esse cillum dolore eu fugiat nulla pariatur. Excepteur sint occaecat cupidatat non proident, sunt in culpa qui officia deserunt mollit anim id est laborum.</p>
  <div class="abs divider"></div>

  <aside>
    <div class="abs flip-box">
      <h3>Lorem Ipsum is not simply<br>random text.</h3>
      <ul>
        <li>quis nostrum exercitationem</li><li>corporis suscipit laboriosam</li><li>vel illum qui dolorem</li><li>velit esse quam nihil</li><li>reprehenderit qui</li>
        <li>quis nostrum exercitationem</li><li>corporis suscipit laboriosam</li><li>vel illum qui dolorem</li><li>velit esse quam nihil</li><li>reprehenderit qui</li>
      </ul>
      <div class="flip-rule"></div>
    </div>
    <div class="abs flip-head">View Our Online Flipbok</div>
    <div class="abs download"><b>DOWNLOAD</b><span>Our Product Guide</span></div>
  </aside>

  <section>
    <article class="abs card" style="left:75px">
      <h2>Products &amp; Services</h2>
      <div class="photo" role="img" aria-label="Workers installing a large blue valve in a pit"></div>
      <p>Contrary to popular belief, Lorem Ipsum is not simply random text. It has roots in a piece of classical Latin literature from 45 BC, making it over 2000 years old. Thomas Wrenfield,</p>
      <div class="more">read more »</div>
    </article>
    <article class="abs card" style="left:330px">
      <h2>Industries Products</h2>
      <div class="photo" role="img" aria-label="Technician assembling a blue pump shaft on site"></div>
      <p>Contrary to popular belief, Lorem Ipsum is not simply random text. It has roots in a piece of classical Latin literature from 45 BC, making it over 2000 years old. Thomas Wrenfield,</p>
      <div class="more">read more »</div>
    </article>
    <article class="abs card" style="left:587px">
      <h2>Get Support</h2>
      <div class="photo" role="img" aria-label="Workers installing a large blue valve in a pit"></div>
      <p>Contrary to popular belief, Lorem Ipsum is not simply random text. It has roots in a piece of classical Latin literature from 45 BC, making it over 2000 years old. Thomas Wrenfield,</p>
      <div class="more">read more »</div>
    </article>
  </section>
</main>

<footer>
  <div class="abs footer"></div>
  <div class="abs foot-nav">Home &nbsp;|&nbsp; About Us &nbsp;|&nbsp; Pump Stations &nbsp;|&nbsp; Pumps &nbsp;|&nbsp; Electrical &nbsp;|&nbsp; Drainage &nbsp;|&nbsp; Environmental &nbsp;|&nbsp; Accessories &nbsp;|&nbsp; Contact Us</div>
  <div class="abs foot-copy">Copyright KelvoRun 2014. All Rights reserved</div>
  <div class="abs foot-credit">Website by Pixel Orchard Studio</div>
</footer>
</body>
</html>
```